Veltrano.co - Polar Expeditions Specialists

We need a modern, visually striking business card for Veltrano.co, a company specialized in selling expedition cruises to the most remote regions on Earth, with a focus on the Arctic and Antarctica. The design should instantly communicate that the cardholder is an expert in polar travel. Use clean, premium aesthetics with cool tones like icy blue and white, possibly incorporating polar imagery (ice, glaciers, penguins, etc.)

Attached the logo

Contact Information for Business Card

Feels high-end and trustworthy.. Visually memorable — encourages people to keep it

Colors
0054AA
0677BA
7BADD7
CADEEF
E8F1F8

Requirements
Must have
• ice, glaciers, penguins, montains
Nice to have
• modern, transparente,

```html
<!DOCTYPE html>
<html lang="en">
<head>
<meta charset="utf-8">
<title>Veltrano.co – Business Card</title>
<link rel="stylesheet" href="https://fonts.googleapis.com/css2?family=Poppins:wght@600;700&family=Montserrat:wght@400;500&display=swap">
<style>
  :root {
    --brand-blue: #3873b8;
    --ink: #1c1c1c;
    --card: #ffffff;
    --backdrop: #e5e4e5;
  }
  * { margin: 0; padding: 0; box-sizing: border-box; }
  html, body { width: 1200px; height: 1108px; overflow: hidden; }
  body { background: var(--backdrop); position: relative; font-family: "Montserrat", sans-serif; }

  .card { position: absolute; background: var(--card); }
  .card-front { left: 219px; top: 50px; width: 774px; height: 473px; }
  .card-back  { left: 217px; top: 568px; width: 776px; height: 457px; }

  .brand { position: absolute; text-align: center; color: var(--brand-blue); }
  .brand-mark { display: block; margin: 0 auto; border-radius: 50%; background: var(--brand-blue); }
  .brand-name { font-family: "Poppins", sans-serif; font-weight: 700; line-height: 1; letter-spacing: -0.5px; white-space: nowrap; }
  .brand-tagline { font-family: "Poppins", sans-serif; font-weight: 600; line-height: 1; white-space: nowrap; }

  .card-front .brand { left: 100px; top: 170px; width: 268px; }
  .card-front .brand-mark { width: 54px; height: 54px; margin-bottom: 52px; }
  .card-front .brand-name { font-size: 43px; letter-spacing: -0.8px; }
  .card-front .brand-tagline { font-size: 15.5px; margin-top: 12px; }

  .divider { position: absolute; left: 382px; top: 162px; width: 2px; height: 200px; background: var(--brand-blue); }

  .contact { position: absolute; left: 402px; top: 160px; color: var(--ink); }
  .contact-name { font-family: "Poppins", sans-serif; font-weight: 600; font-size: 28px; color: var(--brand-blue); line-height: 1.15; }
  .contact-role { font-size: 17px; line-height: 1.2; margin-bottom: 14px; }
  .contact-list { list-style: none; }
  .contact-list li { display: flex; align-items: center; font-size: 17px; height: 30px; }
  .contact-list svg { width: 17px; height: 17px; margin-right: 9px; fill: var(--brand-blue); }
  .contact-address { font-size: 17px; line-height: 22px; margin-top: 6px; }

  .card-back .brand { left: 0; top: 140px; width: 100%; }
  .card-back .brand-mark { width: 66px; height: 66px; margin-bottom: 58px; }
  .card-back .brand-name { font-size: 62px; }
  .card-back .brand-tagline { font-size: 20px; margin-top: 12px; }
</style>
</head>
<body>
  <section class="card card-front">
    <div class="brand">
      <span class="brand-mark"></span>
      <div class="brand-name">Veltrano.co</div>
      <div class="brand-tagline">Polar Expeditions Specialists</div>
    </div>
    <div class="divider"></div>
    <div class="contact">
      <div class="contact-name">Marco Lindqvist</div>
      <div class="contact-role">Managing Director</div>
      <ul class="contact-list">
        <li><svg viewBox="0 0 24 24"><path d="M6.6 10.8a15.1 15.1 0 0 0 6.6 6.6l2.2-2.2a1 1 0 0 1 1-.25 11.4 11.4 0 0 0 3.6.57 1 1 0 0 1 1 1V20a1 1 0 0 1-1 1A17 17 0 0 1 3 4a1 1 0 0 1 1-1h3.5a1 1 0 0 1 1 1c0 1.25.2 2.45.57 3.6a1 1 0 0 1-.25 1z"/></svg>(555)214-7730</li>
        <li><svg viewBox="0 0 24 24"><path d="M3 7.5l9 6 9-6V18H3z M3 6h18l-9 6z"/></svg>info@veltrano.co</li>
        <li><svg viewBox="0 0 24 24"><circle cx="12" cy="12" r="9" fill="none" stroke="#3873b8" stroke-width="2"/><path d="M3 12h18M12 3c3 3 3 15 0 18M12 3c-3 3-3 15 0 18" fill="none" stroke="#3873b8" stroke-width="1.6"/></svg>www.veltrano.co</li>
      </ul>
      <div class="contact-address">42 Harbor View Plaza<br>Lakefield, NJ 07811 USA</div>
    </div>
  </section>

  <section class="card card-back">
    <div class="brand">
      <span class="brand-mark"></span>
      <div class="brand-name">Veltrano.co</div>
      <div class="brand-tagline">Polar Expeditions Specialists</div>
    </div>
  </section>
</body>
</html>
```